tri fold solar sales brochure

Looking for a solar brochure that gives some information but is a teaser to get people to contact me for more information. Something that people will see and want to pickup.
Updates

Target Market(s)

homeowners, middle income

Industry/Entity Type

Sales

Requirements
Must have
• 1) At end of back page

Contact
Mark Tellion
519-736-4082
mtellion@brightroofco.ca

2) We offer a complete all inclusive package from initial application to installation and lifetime monitoring to maximize your return on investment.

3) With a 20 year contract with the KRB you can make a monthly income of $500 to $700.

4) Going off the grid is also an option,you put just enough solar panels on your roof to bring your household consumption of electricity to zero.

5) Net metering is when you install solar panels on your roof to power your household and sell the excess to hydro

6) pictures...header on top of first page.. solar spill on front page I think eyecatching ( you know better though just a thought)

Nice to have
• Mortgage 1- 200,000 with 30 year amortization at 3.89% is $915.16 a month house paid off in 30 years

Mortgage 2 - 240,000 with 30 year amortization at 3.89% is $1102.89 if you had installed solar panels and put money earned each year down on mortgage your house would be paid off in 15 years 6 months and you would still be making money in last 5 years.

Solar just makes sense its that simple

```html
<!DOCTYPE html>
<html lang="en">
<head>
<meta charset="utf-8">
<title>Bright Roof Co – Solar Tri-fold Brochure</title>
<link href="https://fonts.googleapis.com/css2?family=Cinzel:wght@700&family=Exo+2:ital,wght@0,500;0,600;1,500&family=Questrial&family=Roboto+Condensed:wght@400;700&display=swap" rel="stylesheet">
<style>
  :root {
    --navy: #242a6e;
    --navy-deep: #1b1f5e;
    --sky: #3a9ad8;
    --ink-blue: #2b2fa0;
    --accent-blue: #2a64b8;
    --contact-blue: #3a7fc4;
    --text: #2d2d2d;
    --paper: #ffffff;
    --paper-shade: #f1f2f4;
    --fold: #d6d8dc;
  }
  * { margin: 0; padding: 0; box-sizing: border-box; }
  html, body { width: 1200px; height: 942px; overflow: hidden; background: var(--paper); }
  .brochure {
    position: relative; width: 1200px; height: 942px;
    background: linear-gradient(180deg, var(--paper-shade) 0%, var(--paper) 18%, var(--paper) 82%, var(--paper-shade) 100%);
    color: var(--text);
  }
  .shapes { position: absolute; inset: 0; }
  .fold { position: absolute; top: 0; width: 1px; height: 942px; background: var(--fold); }
  .fold--one { left: 400px; } .fold--two { left: 801px; }

  .section-title {
    position: absolute; left: 32px; top: 52px;
    font: 400 25px/38px "Roboto Condensed", sans-serif; color: #fff;
  }
  .mortgage-notes {
    position: absolute; left: 35px; top: 108px; width: 328px;
    font: 18.5px/21.7px "Questrial", sans-serif; letter-spacing: 0.2px;
    text-align: justify; color: var(--text);
  }
  .mortgage-notes p + p { margin-top: 21px; }

  .brand { position: absolute; font-family: "Questrial", sans-serif; color: #333; letter-spacing: 0.5px; white-space: nowrap; }
  .brand--left { left: 0; width: 400px; text-align: center; top: 404px; font-size: 21px; }
  .brand--right { left: 801px; width: 399px; text-align: center; top: 78px; font-size: 26px; }

  .net-metering {
    position: absolute; left: 0; width: 400px; top: 462px; text-align: center;
    font: 400 25px/29px "Roboto Condensed", sans-serif; color: var(--ink-blue);
  }
  .footer-contact {
    position: absolute; left: 76px; top: 890px; display: flex; align-items: center; gap: 10px;
    font: 700 21px/1 "Roboto Condensed", sans-serif; color: #fff; letter-spacing: 0.3px;
  }
  .footer-contact .divider { width: 1px; height: 24px; background: #fff; margin: 0 2px; }

  .income-ribbon {
    position: absolute; left: 452px; top: 161px; width: 320px; text-align: center;
    font: 500 19.5px/25.5px "Exo 2", sans-serif; color: #fff;
  }
  .team-pitch {
    position: absolute; left: 400px; width: 401px; top: 584px; text-align: center;
    font: italic 500 17px/21.8px "Exo 2", sans-serif; color: var(--ink-blue);
  }
  .contact-block { position: absolute; left: 400px; width: 401px; top: 722px; text-align: center; }
  .contact-block__label { font: 15px/1 "Exo 2", sans-serif; letter-spacing: 3px; color: var(--contact-blue); }
  .contact-block__name { margin-top: 14px; font: 600 15px/1 "Exo 2", sans-serif; color: #111; }
  .contact-block__line {
    margin-top: 9px; font: 500 13.5px/1 "Exo 2", sans-serif; color: #222;
    display: flex; justify-content: center; align-items: center; gap: 5px;
  }
  .contact-block__line svg { width: 13px; height: 13px; }

  .offer {
    position: absolute; left: 806px; width: 390px; top: 608px; text-align: center;
    font: 700 23px/29.5px "Cinzel", serif; color: var(--accent-blue);
  }
  .web-band {
    position: absolute; left: 801px; width: 399px; top: 878px; display: flex; justify-content: center; align-items: center; gap: 12px;
    font: 400 20px/1 "Questrial", sans-serif; color: #fff; letter-spacing: 4px;
  }
  .web-band svg { width: 18px; height: 18px; }
</style>
</head>
<body>
<main class="brochure">
  <svg class="shapes" width="1200" height="942" viewBox="0 0 1200 942" xmlns="http://www.w3.org/2000/svg">
    <defs>
      <linearGradient id="band-left" x1="0" x2="1" y1="0" y2="0">
        <stop offset="0" stop-color="#242a6e"/><stop offset="0.55" stop-color="#2a4c9a"/><stop offset="1" stop-color="#3aa6de"/>
      </linearGradient>
      <linearGradient id="ribbon" x1="0" x2="1" y1="1" y2="0">
        <stop offset="0" stop-color="#1f2466"/><stop offset="0.5" stop-color="#254aa0"/><stop offset="1" stop-color="#36a0dc"/>
      </linearGradient>
      <linearGradient id="mid-band" x1="0" x2="1">
        <stop offset="0" stop-color="#2a5fae"/><stop offset="1" stop-color="#3aa2dc"/>
      </linearGradient>
      <linearGradient id="mid-wave" x1="0" x2="1">
        <stop offset="0" stop-color="#1f6bc4"/><stop offset="1" stop-color="#1d3f93"/>
      </linearGradient>
      <linearGradient id="array-photo" x1="0" x2="0" y1="0" y2="1">
        <stop offset="0" stop-color="#c9d2dc"/><stop offset="0.35" stop-color="#3d5ea6"/><stop offset="0.72" stop-color="#34507f"/><stop offset="1" stop-color="#4c6a3a"/>
      </linearGradient>
      <linearGradient id="roof-photo" x1="0" x2="1" y1="0" y2="1">
        <stop offset="0" stop-color="#a9c3dc"/><stop offset="0.35" stop-color="#4a5a86"/><stop offset="0.65" stop-color="#3a3f52"/><stop offset="1" stop-color="#8b6650"/>
      </linearGradient>
    </defs>

    <path d="M0 49 H382 Q392 49 399 58 L428 94 H0 Z" fill="url(#band-left)"/>

    <rect x="0" y="603" width="400" height="278" fill="url(#array-photo)" role="img" aria-label="Photo of a pole-mounted solar panel array in front of evergreen trees"/>

    <polygon points="400,174 1200,174 1200,503 1108,573 400,573" fill="url(#roof-photo)" role="img" aria-label="Photo of a brick house roof covered with solar panels under a blue sky"/>

    <polygon points="777,144 799,174 777,174" fill="#111"/>
    <polygon points="506,144 777,144 777,286 400,286 400,226" fill="url(#ribbon)"/>

    <path d="M0 881 H645 Q628 918 610 924 H0 Z" fill="url(#band-left)"/>
    <path d="M400 881 H645 Q628 918 610 924 H400 Z" fill="url(#mid-band)"/>
    <path d="M627 924 Q640 862 690 861 H801 V924 Z" fill="url(#mid-wave)"/>
    <rect x="801" y="861" width="399" height="63" fill="var(--navy-deep)"/>
  </svg>

  <div class="fold fold--one"></div>
  <div class="fold fold--two"></div>

  <!-- Left panel -->
  <h2 class="section-title">Two types of Mortgages Plan</h2>
  <div class="mortgage-notes">
    <p>Mortgage 1- 200,000 with 30 year amortization at 3.89% is $915.16 a month house paid off in 30 years</p>
    <p>Mortgage 2 - 240,000 with 30 year amortization at 3.89% is $1102.89 if you had installed solar panels and put money earned each year down on mortgage your house would be paid off in 15 years 6 months and you would still be making money in last 5 years.</p>
  </div>
  <p class="brand brand--left">Bright Roof Co</p>
  <p class="net-metering">Net metering is when you<br>install solar panels on your<br>roof to power your household<br>and sell the excess to hydro</p>
  <div class="footer-contact">
    <svg width="24" height="24" viewBox="0 0 24 24"><circle cx="12" cy="12" r="10.5" fill="none" stroke="#fff" stroke-width="1.6"/><path d="M9 7c-1 .5-1.6 1.6-1 3.2 1 2.8 3 4.8 5.6 5.8 1.5.5 2.6-.1 3.1-1l-1.8-1.6-1.4.8c-1.3-.6-2.4-1.7-3-3l.8-1.4L9.7 7z" fill="#fff"/></svg>
    <span>519-736-4082</span><span class="divider"></span><span>Mark Tellion</span>
  </div>

  <!-- Middle panel -->
  <p class="income-ribbon">With a 20 year contract<br>with the KRB you can make<br>a monthly income<br>of $500 to $700</p>
  <p class="team-pitch">We’re an energetic, flexible,<br>and open-minded team ready to<br>work hard for our clients. If<br>you’reinterested in working with us,<br>please send us a message!</p>
  <div class="contact-block">
    <p class="contact-block__label">Contact</p>
    <p class="contact-block__name">Mark Tellion</p>
    <p class="contact-block__line"><svg viewBox="0 0 16 16"><path d="M2 6c0-2 3-3 6-3s6 1 6 3v1h-3V5.5H5V7H2z M4 8h8l1 5H3z" fill="var(--ink-blue)"/></svg>519-736-4082</p>
    <p class="contact-block__line"><svg viewBox="0 0 16 16"><rect x="1.5" y="3.5" width="13" height="9" fill="none" stroke="var(--ink-blue)" stroke-width="1.3"/><path d="M1.5 3.5 8 9l6.5-5.5" fill="none" stroke="var(--ink-blue)" stroke-width="1.3"/></svg>mtellion@brightroofco.ca</p>
    <p class="contact-block__line"><svg viewBox="0 0 16 16"><circle cx="8" cy="8" r="6.5" fill="none" stroke="#4a6fa8" stroke-width="1.2"/><ellipse cx="8" cy="8" rx="3" ry="6.5" fill="none" stroke="#4a6fa8" stroke-width="1"/><path d="M1.5 8h13M2.5 5h11M2.5 11h11" stroke="#4a6fa8" stroke-width="1"/></svg>www.brightroofco.ca</p>
  </div>

  <!-- Right panel -->
  <p class="brand brand--right">Bright Roof Co</p>
  <p class="offer">We offer a complete<br>all inclusive packages<br>from initial application<br>to installation and<br>lifetime monitoring to<br>maximize your return<br>on investment.</p>
  <div class="web-band">
    <svg viewBox="0 0 16 16"><circle cx="8" cy="8" r="6.5" fill="none" stroke="#fff" stroke-width="1.2"/><ellipse cx="8" cy="8" rx="3" ry="6.5" fill="none" stroke="#fff" stroke-width="1"/><path d="M1.5 8h13M2.5 5h11M2.5 11h11" stroke="#fff" stroke-width="1"/></svg>
    <span>www.brightroofco.ca</span>
  </div>
</main>
</body>
</html>
```